RW Holloway LLC Business Card - Civil Engineering & Consulting Firm

We need a Business Card that is elegant, and masculine.  It is our Professional Civil Engineering & Consulting Company located in San Antonio TX (Not s construction or builder firm- no gears & no tool images please). We provide civil engineering services including  commercial site plans, grading and drainage plans, utility plans, hydraulics and hydrology, land planning, utility coordination, and other general civil engineering services related to commercial and residential development.
We have 2 existing Logos. We would like to convey reliability, strength, trustworthiness and attention to detail.  Blues and orange tones as per logo We are OK with the use of a darker blue in the mix.  We have 2 logo versions - Full Company Name Logo to go on the back of card, & Small Icon Logo for the front w/ personal Info.

Target Market(s)
Architects, Real Estate Developers, Other Strctural Engineers, Surveyers, General Contractors
Industry/Entity Type
Professional Civil Engineering
Contact Information for Business Card
Name, Position, Address, Cell & Office #, email, and company website
Font styles to use
Other font styles liked:
- Avian
Requirements
Should not have
- No Tools, No Gears, no Cranes, or Construction Equipment.

```html
<!DOCTYPE html>
<html lang="en">
<head>
<meta charset="utf-8">
<title>RW Holloway LLC – Business Card</title>
<link rel="stylesheet" href="https://fonts.googleapis.com/css2?family=Montserrat:wght@300;400;500;700&display=swap">
<style>
  :root {
    --stage: #3a3b3d;
    --card: #ffffff;
    --card-shade: #f1f1f1;
    --sky-blue: #6fa8dc;
    --orange: #f0901e;
    --ink: #1d1d1f;
  }
  * { margin: 0; padding: 0; box-sizing: border-box; }
  html, body { width: 1200px; height: 1012px; overflow: hidden; }
  body {
    background: var(--stage);
    font-family: "Montserrat", Arial, sans-serif;
    color: var(--ink);
    position: relative;
  }
  .card {
    position: absolute;
    left: 290px;
    width: 620px;
    height: 354px;
    background: linear-gradient(135deg, var(--card) 60%, var(--card-shade));
    box-shadow: 0 14px 30px rgba(0,0,0,.45);
  }
  .card--front { top: 112px; }
  .card--back { top: 546px; }

  /* Front side */
  .brand-lockup {
    position: absolute;
    left: 0; right: 0; top: 138px;
    display: flex;
    align-items: center;
    justify-content: center;
    gap: 16px;
  }
  .brand-mark {
    width: 22px; height: 22px;
    background: var(--orange);
  }
  .brand-name {
    font-weight: 300;
    font-size: 44px;
    letter-spacing: 3px;
    color: var(--sky-blue);
    text-transform: uppercase;
  }
  .brand-rule {
    position: absolute;
    left: 130px; right: 130px; top: 214px;
    height: 2px;
    background: var(--sky-blue);
  }

  /* Back side */
  .back-brand {
    position: absolute;
    left: 40px; top: 0; bottom: 0;
    width: 210px;
    display: flex;
    align-items: center;
    gap: 12px;
  }
  .back-brand .brand-mark { width: 16px; height: 16px; flex: none; }
  .back-brand .brand-name {
    font-size: 20px;
    letter-spacing: 1.5px;
    line-height: 1.3;
  }
  .divider {
    position: absolute;
    left: 268px; top: 62px;
    width: 2px; height: 232px;
    background: var(--orange);
  }
  .contact {
    position: absolute;
    left: 300px; top: 64px;
    font-size: 15px;
    line-height: 1.3;
  }
  .contact__name {
    font-weight: 700;
    font-size: 19px;
    color: var(--orange);
    text-transform: uppercase;
    letter-spacing: .5px;
  }
  .contact__role { font-size: 15px; margin-bottom: 18px; }
  .contact__address { margin-bottom: 16px; }
  .contact__list { list-style: none; }
  .contact__list li {
    display: flex;
    align-items: center;
    gap: 10px;
    margin-bottom: 2px;
  }
  .contact__list svg { width: 14px; height: 14px; flex: none; fill: var(--orange); }
</style>
</head>
<body>

<section class="card card--front" aria-label="Card front">
  <div class="brand-lockup">
    <span class="brand-mark"></span>
    <span class="brand-name">RW Holloway LLC</span>
  </div>
  <div class="brand-rule"></div>
</section>

<section class="card card--back" aria-label="Card back">
  <div class="back-brand">
    <span class="brand-mark"></span>
    <span class="brand-name">RW Holloway LLC</span>
  </div>
  <div class="divider"></div>
  <div class="contact">
    <p class="contact__name">Daniel Reyes</p>
    <p class="contact__role">Co-Founder</p>
    <p class="contact__address">4810 Alamo Ridge Road<br>Suite 210 San Antonio, TX</p>
    <ul class="contact__list">
      <li>
        <svg viewBox="0 0 24 24" aria-hidden="true"><path d="M6.6 10.8a15 15 0 0 0 6.6 6.6l2.2-2.2a1 1 0 0 1 1-.25 11.4 11.4 0 0 0 3.6.57 1 1 0 0 1 1 1V20a1 1 0 0 1-1 1A17 17 0 0 1 3 4a1 1 0 0 1 1-1h3.5a1 1 0 0 1 1 1c0 1.25.2 2.45.57 3.57a1 1 0 0 1-.25 1z"/></svg>
        210-555-0142
      </li>
      <li>
        <svg viewBox="0 0 24 24" aria-hidden="true"><path d="M3 8c0-2 4-4 9-4s9 2 9 4v2h-5V8H8v2H3zM5 12h14l1 8H4zm7 2a2.5 2.5 0 1 0 0 5 2.5 2.5 0 0 0 0-5z"/></svg>
        210-555-0178
      </li>
      <li>
        <svg viewBox="0 0 24 24" aria-hidden="true"><path d="M2 5h20v14H2zm2 2v.5l8 5.5 8-5.5V7z"/></svg>
        info@rwhollowayllc.com
      </li>
      <li>
        <svg viewBox="0 0 24 24" aria-hidden="true"><circle cx="12" cy="12" r="10"/></svg>
        www.rwhollowayllc.com
      </li>
    </ul>
  </div>
</section>

</body>
</html>
```